Brightarc Orthodontics appointment card design

I need appointment cards/ business cards made. Front will be Logo, name, title, email, phone number and location (5263 Walnut Hollow Pkwy, Ste 412, Concord, NC 28027) . the back should have an appointment card (name, time, date) and also 3 addresses listed with a check box so we can check to which location they are going.
Dale Fenwick Orthodontics
- 6735 Orchard Street, Ste 514, Harrisburg, NC 28075
- 3647 Ridgeway Drive NE, Ste 810, Concord, NC 28025
- 2917 Thornbury Corporate Drive, Ste 605, Charlotte, NC 28277
Business card can be horizontal or vertical in Design.
I need to be able to edit it to update and add new employees

Requirements
Must have
• Front:
• - Logo
• - Name & Title (able to be edited)
• - phone (704-555-0186) & Email (need to be able to edit)
• - Address: 5263 Walnut Hollow Pkwy, Ste 412
• Concord, NC 28027
• Back:
• Appointment Card design:
• - Name, time, Date
• - 3 locations w/ a check box so the patient knows where to go:
• Dale Fenwick Orthodontics
• - 6735 Orchard Street, Ste 514, Harrisburg, NC 28075
• - 3647 Ridgeway Drive NE, Ste 810, Concord, NC 28025
• - 2917 Thornbury Corporate Drive, Ste 605, Charlotte, NC 28277

```html
<!DOCTYPE html>
<html lang="en">
<head>
<meta charset="UTF-8">
<title>Brightarc Orthodontics – Appointment &amp; Business Card</title>
<link href="https://fonts.googleapis.com/css2?family=Roboto:wght@400;500;700&display=swap" rel="stylesheet">
<style>
  :root {
    --bg: #4a4b4e;
    --card: #ffffff;
    --brand-blue: #1169ad;
    --accent-grey: #8a8c8f;
    --ink: #4a4a4a;
    --rule: #555555;
  }
  * { box-sizing: border-box; margin: 0; padding: 0; }
  html, body { width: 1200px; height: 1000px; overflow: hidden; }
  body {
    background: var(--bg);
    font-family: "Roboto", Arial, sans-serif;
    color: var(--ink);
    position: relative;
  }
  .card {
    position: absolute;
    width: 720px;
    height: 410px;
    background: var(--card);
    border-radius: 26px;
    overflow: hidden;
    box-shadow: 0 14px 30px rgba(0,0,0,.35);
  }

  /* ---------- Appointment side ---------- */
  .appointment { left: 420px; top: 50px; }
  .appointment .top-band {
    position: absolute; left: 0; top: 0; width: 100%; height: 16px;
    background: var(--brand-blue);
  }
  .appointment .heading {
    position: absolute; left: 40px; top: 48px;
    color: var(--brand-blue); font-weight: 700; font-size: 21px;
  }
  .field {
    position: absolute; display: flex; align-items: flex-end;
    font-size: 14px; color: var(--ink);
  }
  .field .label { margin-right: 8px; }
  .field .line { flex: 1; border-bottom: 1.5px solid var(--rule); height: 1px; margin-bottom: 3px; }
  .field-name { left: 40px; top: 98px; width: 390px; }
  .field-date { left: 40px; top: 138px; width: 640px; }
  .field-time { left: 40px; top: 186px; width: 640px; }
  .field-time .lead { flex: 1.1; border-bottom: 1.5px solid var(--rule); margin-right: 10px; margin-bottom: 3px; }
  .ampm {
    position: absolute; top: 214px; right: 40px;
    display: flex; gap: 20px; font-size: 14px;
  }
  .checkbox {
    display: inline-block; width: 15px; height: 15px;
    border: 1.5px solid var(--brand-blue); vertical-align: -2px; margin-right: 5px;
  }
  .wordmark-small {
    position: absolute; right: 40px; top: 72px;
    display: flex; align-items: center; gap: 10px;
    color: var(--brand-blue); font-weight: 700; font-size: 26px; line-height: 1.05;
  }
  .wordmark-dot { width: 16px; height: 16px; border-radius: 50%; background: var(--brand-blue); flex: none; }
  .practice-name {
    position: absolute; left: 0; width: 100%; top: 262px; text-align: center;
    font-size: 14px;
  }
  .practice-name strong { color: var(--brand-blue); font-size: 20px; font-weight: 700; }
  .locations {
    position: absolute; left: 26px; right: 26px; top: 300px;
    display: flex; justify-content: space-between; text-align: center;
    font-size: 12.5px; line-height: 1.35;
  }
  .location { width: 215px; }
  .location .checkbox { display: block; margin: 0 auto 6px; }

  /* ---------- Business side ---------- */
  .business { left: 80px; top: 530px; }
  .wordmark-large {
    position: absolute; left: 46px; top: 48px;
    display: flex; align-items: center; gap: 16px;
    color: var(--brand-blue); font-weight: 700; font-size: 46px; line-height: 1.05;
  }
  .wordmark-large .wordmark-dot { width: 26px; height: 26px; }
  .person {
    position: absolute; right: 60px; top: 128px; text-align: right;
  }
  .person .name { color: var(--brand-blue); font-weight: 700; font-size: 21px; letter-spacing: .3px; }
  .person .title { font-size: 15px; margin-top: 2px; }
  .wave { position: absolute; left: 0; top: 0; width: 720px; height: 410px; }
  .contact {
    position: absolute; right: 46px; bottom: 22px; text-align: right;
    color: #fff; font-size: 15px; line-height: 1.35;
  }
  .contact .address { margin-bottom: 10px; }
  .contact .row { display: flex; justify-content: flex-end; align-items: center; gap: 10px; }
  .contact svg { width: 15px; height: 15px; }
</style>
</head>
<body>

<section class="card appointment">
  <div class="top-band"></div>
  <h2 class="heading">Next Appointment</h2>

  <div class="field field-name"><span class="label">Name</span><span class="line"></span></div>
  <div class="field field-date"><span class="label">Date</span><span class="line"></span></div>
  <div class="field field-time"><span class="lead"></span><span class="label">Time</span><span class="line"></span></div>
  <div class="ampm">
    <span><span class="checkbox"></span>AM</span>
    <span><span class="checkbox"></span>PM</span>
  </div>

  <div class="wordmark-small">
    <span class="wordmark-dot"></span>
    <span>Brightarc<br>Orthodontics</span>
  </div>

  <p class="practice-name"><strong>Dale Fenwick</strong> Orthodontics</p>

  <div class="locations">
    <div class="location"><span class="checkbox"></span>6735 Orchard Street, Ste 514,<br>Harrisburg, NC 28075</div>
    <div class="location"><span class="checkbox"></span>3647 Ridgeway Drive NE, Ste 810,<br>Concord, NC 28025</div>
    <div class="location"><span class="checkbox"></span>2917 Thornbury Corporate Drive,<br>Ste 605, Charlotte, NC 28277</div>
  </div>
</section>

<section class="card business">
  <svg class="wave" viewBox="0 0 720 410" preserveAspectRatio="none" aria-hidden="true">
    <path d="M0 238 C 130 318, 270 360, 390 358 C 270 372, 130 350, 0 268 Z" fill="var(--accent-grey)"/>
    <path d="M0 285 C 120 370, 260 392, 380 362 C 470 340, 540 210, 720 190 L720 410 L0 410 Z" fill="var(--brand-blue)"/>
  </svg>

  <div class="wordmark-large">
    <span class="wordmark-dot"></span>
    <span>Brightarc<br>Orthodontics</span>
  </div>

  <div class="person">
    <div class="name">DALE FENWICK</div>
    <div class="title">Orthodontics</div>
  </div>

  <div class="contact">
    <div class="address">5263 Walnut Hollow Pkwy,<br>Ste 412 - Concord, NC 28027</div>
    <div class="row">704-555-0186
      <svg viewBox="0 0 24 24" aria-hidden="true"><path fill="#fff" d="M6.6 10.8a15 15 0 0 0 6.6 6.6l2.2-2.2c.3-.3.7-.4 1-.2 1.1.4 2.3.6 3.6.6.6 0 1 .4 1 1V20c0 .6-.4 1-1 1A17 17 0 0 1 3 4c0-.6.4-1 1-1h3.5c.6 0 1 .4 1 1 0 1.3.2 2.5.6 3.6.1.3 0 .7-.2 1z"/></svg>
    </div>
    <div class="row">dalefenwick@brightarcmail.com
      <svg viewBox="0 0 24 24" aria-hidden="true"><path fill="#fff" d="M3 5h18v14H3z"/><path fill="none" stroke="var(--brand-blue)" stroke-width="2" d="M3 6l9 7 9-7"/></svg>
    </div>
  </div>
</section>

</body>
</html>
```